Global (re)insurance broker needs a business card design

We need a classic business card for our company that is headquartered in SG, with offices in Malaysia and Dubai. We specialise in insurance and reinsurance broking and consultancy for our global clients.

```html
<!DOCTYPE html>
<html lang="en">
<head>
<meta charset="utf-8">
<title>Norvale Business Card</title>
<link rel="stylesheet" href="https://fonts.googleapis.com/css2?family=Open+Sans:wght@400;600;700&display=swap">
<style>
  :root {
    --page: #e9e9ec;
    --card: #1f1f23;
    --brand-blue: #2547a0;
    --brand-green: #c4dfb9;
    --text-light: #ffffff;
    --shadow: rgba(0, 0, 0, 0.18);
  }
  * { margin: 0; padding: 0; box-sizing: border-box; }
  html, body {
    width: 1200px;
    height: 780px;
    overflow: hidden;
    background: var(--page);
    font-family: "Open Sans", Arial, sans-serif;
  }
  .stage {
    position: relative;
    width: 1200px;
    height: 780px;
  }
  .card {
    position: absolute;
    top: 235px;
    width: 540px;
    height: 310px;
    background: var(--card);
    overflow: hidden;
    box-shadow: 0 8px 24px var(--shadow);
  }
  .card--front { left: 40px; }
  .card--back { left: 620px; }

  .card__band {
    position: absolute;
    inset: 0;
    width: 540px;
    height: 310px;
  }
  .band-fill { fill: var(--brand-blue); }
  .band-line { fill: none; stroke: var(--brand-green); stroke-width: 4; stroke-linecap: round; }

  .wordmark {
    position: absolute;
    font-weight: 700;
    color: var(--brand-green);
    letter-spacing: 2px;
    line-height: 1;
  }
  .card--front .wordmark { left: 250px; top: 62px; font-size: 54px; }
  .card--back .wordmark {
    left: 0; right: 0; top: 118px;
    text-align: center;
    font-size: 72px;
  }

  .holder {
    position: absolute;
    left: 58px;
    top: 118px;
  }
  .holder__name {
    font-size: 28px;
    font-weight: 700;
    color: var(--brand-blue);
    line-height: 1.1;
  }
  .holder__title {
    font-size: 13px;
    color: var(--text-light);
    margin-top: 2px;
  }

  .divider {
    position: absolute;
    left: 262px;
    top: 158px;
    width: 2px;
    height: 70px;
    background: var(--text-light);
  }

  .contacts {
    position: absolute;
    left: 278px;
    top: 160px;
    list-style: none;
  }
  .contacts li {
    display: flex;
    align-items: center;
    gap: 8px;
    font-size: 13px;
    color: var(--text-light);
    height: 22px;
  }
  .contacts svg { width: 12px; height: 12px; flex: none; }
  .icon-stroke { fill: none; stroke: var(--text-light); stroke-width: 1.5; }
  .icon-fill { fill: var(--brand-blue); }

  .address {
    position: absolute;
    left: 26px;
    bottom: 10px;
    font-size: 13px;
    color: var(--text-light);
  }
</style>
</head>
<body>
<main class="stage">

  <section class="card card--front" aria-label="Business card front">
    <svg class="card__band" viewBox="0 0 540 310" aria-hidden="true">
      <path class="band-fill" d="M0,178 C120,262 330,284 540,272 L540,310 L0,310 Z"/>
      <path class="band-line" d="M48,160 C150,245 340,268 520,258"/>
    </svg>

    <div class="wordmark">NORVALE</div>

    <div class="holder">
      <div class="holder__name">Mira Lowe</div>
      <div class="holder__title">Chief Operating Officer</div>
    </div>

    <div class="divider"></div>

    <ul class="contacts">
      <li>
        <svg viewBox="0 0 12 12" aria-hidden="true"><rect class="icon-stroke" x="3" y="1" width="6" height="10" rx="1"/></svg>
        +65 9123 4567
      </li>
      <li>
        <svg viewBox="0 0 12 12" aria-hidden="true"><circle class="icon-fill" cx="6" cy="6" r="5.5"/></svg>
        www.norvale-re.com
      </li>
      <li>
        <svg viewBox="0 0 12 12" aria-hidden="true"><rect class="icon-stroke" x="1" y="2.5" width="10" height="7"/><path class="icon-stroke" d="M1,2.5 L6,7 L11,2.5"/></svg>
        mira@norvale-re.com
      </li>
    </ul>

    <div class="address">28 Harbour Street, Marina Tower #12-04, Singapore 018956</div>
  </section>

  <section class="card card--back" aria-label="Business card back">
    <div class="wordmark">NORVALE</div>
  </section>

</main>
</body>
</html>
```